BoltRidge construction business cards

I need a business card with a replacement window photo or graphic on it .phone # 919 482 -7036 boltridgeconstruction@mailvessel.com fax #919 274-8815 '' The Window Replacement Specialist"

Construction

```html
<!DOCTYPE html>
<html lang="en">
<head>
<meta charset="utf-8">
<title>BoltRidge Construction – Business Card</title>
<link rel="stylesheet" href="https://fonts.googleapis.com/css2?family=Oswald:wght@600&family=Roboto+Condensed:wght@400;700&display=swap">
<style>
  :root {
    --backdrop: #353434;
    --card-green: #6cbe52;
    --card-white: #ffffff;
    --ink: #2b2b2b;
    --label-white: #ffffff;
  }
  * { margin: 0; padding: 0; box-sizing: border-box; }
  html, body { width: 961px; height: 1200px; overflow: hidden; }
  body {
    position: relative;
    background: var(--backdrop);
    font-family: "Roboto Condensed", "Arial Narrow", sans-serif;
  }
  .side-label {
    position: absolute;
    left: 32px;
    color: var(--label-white);
    font-family: Arial, Helvetica, sans-serif;
    font-weight: 700;
    font-size: 30px;
    letter-spacing: 1px;
    transform: translate(-50%, -50%) rotate(-90deg);
    white-space: nowrap;
  }
  .side-label--front { top: 322px; }
  .side-label--back { top: 872px; }

  .card {
    position: absolute;
    left: 72px;
    width: 816px;
    height: 478px;
    overflow: hidden;
  }
  .card--front { top: 85px; background: var(--card-green); }
  .card--back { top: 636px; background: var(--card-white); }

  .mascot-art {
    position: absolute;
    background: radial-gradient(ellipse at 50% 45%, #f4f4f4 0%, #cfcfcf 45%, #555 100%);
    border-radius: 6px;
    opacity: 0.85;
  }
  .card--front .mascot-art { left: 171px; top: 95px; width: 265px; height: 285px; }
  .card--back .mascot-art { left: 593px; top: 232px; width: 180px; height: 190px; }

  .tagline-stack {
    position: absolute;
    left: 441px;
    top: 226px;
    font-family: "Oswald", "Arial Narrow", sans-serif;
    font-weight: 600;
    color: var(--ink);
    font-size: 33px;
    line-height: 38px;
    letter-spacing: 0.5px;
    text-transform: uppercase;
  }

  .brand-name {
    position: absolute;
    left: 118px;
    top: 100px;
    font-family: "Roboto Condensed", "Arial Narrow", sans-serif;
    font-weight: 700;
    font-size: 88px;
    line-height: 1;
    color: var(--card-green);
  }

  .contact-band {
    position: absolute;
    left: 0; top: 248px;
    width: 100%; height: 132px;
    background: var(--card-green);
  }
  .contact-list {
    position: absolute;
    left: 119px;
    top: 22px;
    font-size: 23px;
    line-height: 31px;
    color: var(--ink);
    list-style: none;
  }
  .contact-list li { display: flex; }
  .contact-list .label { width: 67px; }
  .contact-list .sep { width: 20px; }

  .tagline-strip {
    position: absolute;
    left: 44px;
    top: 388px;
    font-family: "Oswald", "Arial Narrow", sans-serif;
    font-weight: 600;
    font-size: 28px;
    line-height: 40px;
    letter-spacing: 1.5px;
    color: var(--ink);
    text-transform: uppercase;
    white-space: nowrap;
  }
  .bottom-band {
    position: absolute;
    left: 0; top: 436px;
    width: 100%; height: 42px;
    background: var(--card-green);
  }
</style>
</head>
<body>
  <div class="side-label side-label--front">SIDE 1</div>
  <div class="side-label side-label--back">SIDE 2</div>

  <section class="card card--front">
    <div class="mascot-art" role="img" aria-label="Illustration of a cheerful window installer leaning on a window frame in front of gears"></div>
    <p class="tagline-stack">The<br>Window<br>Replacement<br>Specialist</p>
  </section>

  <section class="card card--back">
    <div class="brand-name">BoltRidge</div>
    <div class="contact-band">
      <ul class="contact-list">
        <li><span class="label">Phone</span><span class="sep">:</span><span>919 482 7036</span></li>
        <li><span class="label">Email</span><span class="sep">:</span><span>boltridgeconstruction@mailvessel.com</span></li>
        <li><span class="label">Fax</span><span class="sep">:</span><span>919 274 8815</span></li>
      </ul>
    </div>
    <p class="tagline-strip">The Window Replacement Specialist</p>
    <div class="bottom-band"></div>
    <div class="mascot-art" role="img" aria-label="Small illustration of the window installer leaning on a window frame with gears"></div>
  </section>
</body>
</html>
```